New Business Card Design Project

Use the flyer uploaded and website www.brightoakbuilders.com for inspiration.
List Our Services on Backside of business cards
Marcus Delling
Harborline Builders Inc.
Licensed General Contractors
858-471-6093

Contact Information for Business Card

Use the flyer uploaded and website www.brightoakbuilders.com for inspiration. List Our Services on Backside of business cards Marcus Delling Harborline Builders Inc. Licensed General Contractors 858-471-6093

```html
<!DOCTYPE html>
<html lang="en">
<head>
<meta charset="utf-8">
<title>Harborline Builders Business Card</title>
<link href="https://fonts.googleapis.com/css2?family=Cormorant+Garamond:wght@500&family=Arimo:wght@400&display=swap" rel="stylesheet">
<style>
  :root {
    --backdrop: #d9d9db;
    --card: #ffffff;
    --charcoal: #333333;
    --ink: #1e1e1e;
    --soft-ink: #e6e6e6;
  }
  * { box-sizing: border-box; margin: 0; padding: 0; }
  html, body { width: 1200px; height: 800px; overflow: hidden; }
  body {
    background: var(--backdrop);
    font-family: "Arimo", Arial, sans-serif;
    position: relative;
  }
  .card {
    position: absolute;
    width: 540px;
    height: 310px;
    top: 245px;
    background: var(--card);
    border-radius: 18px;
    overflow: hidden;
    box-shadow: 0 8px 24px rgba(0,0,0,0.18);
  }
  .card--front { left: 45px; }
  .card--back { left: 615px; }

  .front-band { position: absolute; inset: 0; width: 100%; height: 100%; }
  .brand {
    position: absolute;
    left: 28px;
    top: 140px;
    color: var(--soft-ink);
    font-family: "Cormorant Garamond", Georgia, serif;
    font-size: 24px;
    letter-spacing: 2px;
    text-transform: uppercase;
    display: flex;
    align-items: center;
    gap: 10px;
  }
  .brand-dot {
    width: 10px; height: 10px;
    border: 1px solid var(--soft-ink);
    border-radius: 50%;
  }
  .company {
    position: absolute;
    left: 28px;
    top: 212px;
    color: #ffffff;
    font-size: 14px;
    line-height: 1.4;
  }
  .holder-name {
    position: absolute;
    right: 32px;
    top: 26px;
    font-family: "Cormorant Garamond", Georgia, serif;
    font-weight: 500;
    font-size: 23px;
    letter-spacing: 2px;
    text-transform: uppercase;
    color: var(--ink);
  }
  .contact {
    position: absolute;
    right: 28px;
    bottom: 60px;
    list-style: none;
    font-size: 14px;
    color: var(--ink);
    text-align: right;
    line-height: 1.45;
  }
  .contact li { display: flex; align-items: center; justify-content: flex-end; gap: 7px; }
  .contact svg { width: 11px; height: 11px; fill: var(--ink); }

  .services {
    position: absolute;
    left: 26px;
    top: 30px;
    list-style: none;
    font-size: 15px;
    color: var(--ink);
    line-height: 1.47;
  }
  .services li { display: flex; align-items: center; gap: 12px; }
  .services li::before {
    content: "";
    width: 7px; height: 7px;
    background: var(--ink);
    flex: none;
  }
  .back-artwork {
    position: absolute;
    right: 22px;
    top: 40px;
    width: 200px;
    height: 250px;
    border-radius: 6px;
    background: linear-gradient(160deg, #f2f2f2, #dcdcdc);
  }
</style>
</head>
<body>
  <section class="card card--front">
    <svg class="front-band" viewBox="0 0 540 310" aria-hidden="true">
      <polygon points="0,72 340,72 210,310 0,310" fill="var(--charcoal)"/>
    </svg>
    <div class="brand"><span class="brand-dot"></span>Harborline</div>
    <p class="company">Harborline Builders Inc.<br>Licensed General Contractors</p>
    <h1 class="holder-name">Marcus Delling</h1>
    <ul class="contact">
      <li>858-471-6093
        <svg viewBox="0 0 24 24"><path d="M6.6 10.8a15 15 0 0 0 6.6 6.6l2.2-2.2c.3-.3.7-.4 1-.2 1.1.4 2.3.6 3.6.6.6 0 1 .4 1 1V20c0 .6-.4 1-1 1A17 17 0 0 1 3 4c0-.6.4-1 1-1h3.5c.6 0 1 .4 1 1 0 1.3.2 2.5.6 3.6.1.3 0 .7-.2 1z"/></svg>
      </li>
      <li>info@brightoakbuilders.com
        <svg viewBox="0 0 24 24"><path d="M2 5h20v14H2z M2 5l10 8 10-8" /></svg>
      </li>
      <li>www.brightoakbuilders.com
        <svg viewBox="0 0 24 24"><circle cx="12" cy="12" r="10"/></svg>
      </li>
    </ul>
  </section>

  <section class="card card--back">
    <ul class="services">
      <li>Remodeling : Kitchen &amp; Bath</li>
      <li>Painting : Interior &amp; Exterior</li>
      <li>Flooring : Carpet, Vinyl, Wood</li>
      <li>Window &amp; Door Replacement</li>
      <li>Plumbing : Repairs &amp; Upgrades</li>
      <li>Energy- Efficient Upgrades</li>
      <li>Deck &amp; Patio Construction</li>
      <li>Water &amp; Mold Damage</li>
      <li>Garage Renovation</li>
    </ul>
    <div class="back-artwork" role="img" aria-label="Line drawing of a palm tree beside a house outline"></div>
  </section>
</body>
</html>
```